Business Card Design Project - del varosi group

dear Sirs

we need business card design for our group ( DEL Varosi Group ) , i have got the Logo design of our group from pixel harbor in previous , so all need details relating to our group i think available with you, as well as the the chosen logo design

we hope to provide us with business card logo that to be appropaite and satisfactory to us .

thanks

note : logo design of our group is attached .
Updates

Reason: please extend the deadline of my project for additional 15 days because i didn't received appropriate design for our gruop yet . kindly beaware that i have received 77 design till now , supossed to send me 200-250 design at least . thanks

Target Market(s)

contents

name : Kerem EL Nadiri

position : Operation Manager

Industry/Entity Type

Business

Requirements
Must have

• person name

group logo
Nice to have
• logo color matching with back background

```html
<!DOCTYPE html>
<html lang="en">
<head>
<meta charset="utf-8">
<title>DEL Varosi Group – Business Card</title>
<link href="https://fonts.googleapis.com/css2?family=Source+Sans+3:wght@400;600;700&display=swap" rel="stylesheet">
<style>
  :root {
    --stage: #b08c34;
    --card: #ffffff;
    --brand-blue: #1b5e9b;
    --accent-blue: #1b75bb;
    --gold: #c8992e;
    --ink: #1e1e1e;
  }
  * { margin: 0; padding: 0; box-sizing: border-box; }
  html, body { width: 1200px; height: 686px; overflow: hidden; }
  body {
    background: var(--stage);
    font-family: "Source Sans 3", Arial, sans-serif;
    color: var(--ink);
    position: relative;
  }
  .card {
    position: absolute;
    width: 524px;
    height: 298px;
    background: var(--card);
  }
  .card--front { left: 60px; top: 137px; }
  .card--back { left: 609px; top: 289px; }

  .rule {
    position: absolute;
    top: 142px;
    height: 3px;
    background: var(--accent-blue);
  }
  .rule--left { left: 0; width: 36px; }
  .rule--mid { left: 300px; width: 164px; }
  .rule--right { left: 493px; width: 31px; }

  .wordmark {
    position: absolute;
    color: var(--brand-blue);
    font-weight: 600;
    line-height: 1;
    text-transform: uppercase;
  }
  .wordmark__main { display: block; }
  .wordmark__sub { display: block; text-align: right; }

  .card--front .wordmark { left: 50px; top: 116px; width: 232px; }
  .card--front .wordmark__main { font-size: 36px; letter-spacing: 0.5px; }
  .card--front .wordmark__sub { font-size: 15px; letter-spacing: 3px; margin-top: 3px; }

  .card--back .wordmark { left: 104px; top: 113px; width: 316px; }
  .card--back .wordmark__main { font-size: 49px; letter-spacing: 0.8px; }
  .card--back .wordmark__sub { font-size: 20px; letter-spacing: 4px; margin-top: 4px; }

  .details {
    position: absolute;
    right: 60px;
    text-align: right;
  }
  .identity { top: 54px; }
  .person-name { font-size: 16px; font-weight: 700; color: var(--accent-blue); line-height: 20px; }
  .person-role { font-size: 11.5px; font-weight: 700; color: var(--gold); line-height: 15px; }
  .address { font-size: 12.5px; line-height: 15px; margin-top: 8px; }

  .contacts { top: 162px; list-style: none; }
  .contacts li {
    font-size: 12.5px;
    line-height: 18.5px;
    display: flex;
    justify-content: flex-end;
    align-items: center;
    gap: 5px;
  }
  .contacts svg { width: 11px; height: 11px; fill: var(--accent-blue); flex: none; }
</style>
</head>
<body>

<section class="card card--front">
  <div class="rule rule--left"></div>
  <div class="rule rule--mid"></div>
  <div class="rule rule--right"></div>

  <div class="wordmark">
    <span class="wordmark__main">DEL Varosi</span>
    <span class="wordmark__sub">Group</span>
  </div>

  <div class="details identity">
    <p class="person-name">Kerem EL Nadiri</p>
    <p class="person-role">Operation Manager</p>
    <p class="address">Street name City<br>State, zip code</p>
  </div>

  <ul class="details contacts">
    <li>(TF)123-456-7890
      <svg viewBox="0 0 24 24"><path d="M6.6 10.8a15 15 0 0 0 6.6 6.6l2.2-2.2c.3-.3.7-.4 1-.2 1.1.4 2.3.6 3.6.6.6 0 1 .4 1 1V20c0 .6-.4 1-1 1A17 17 0 0 1 3 4c0-.6.4-1 1-1h3.5c.6 0 1 .4 1 1 0 1.3.2 2.5.6 3.6.1.3 0 .7-.2 1z"/></svg>
    </li>
    <li>123-456-7890
      <svg viewBox="0 0 24 24"><path d="M6.6 10.8a15 15 0 0 0 6.6 6.6l2.2-2.2c.3-.3.7-.4 1-.2 1.1.4 2.3.6 3.6.6.6 0 1 .4 1 1V20c0 .6-.4 1-1 1A17 17 0 0 1 3 4c0-.6.4-1 1-1h3.5c.6 0 1 .4 1 1 0 1.3.2 2.5.6 3.6.1.3 0 .7-.2 1z"/></svg>
    </li>
    <li>123-456-7890
      <svg viewBox="0 0 24 24"><path d="M6 2h9l3 3v4H6zM3 10h18v9h-3v3H6v-3H3zm5 6v4h8v-4zm10-4a1 1 0 1 0 0 2 1 1 0 0 0 0-2z"/></svg>
    </li>
    <li>name@website.com
      <svg viewBox="0 0 24 24"><path d="M2 5h20v14H2zm2 2v.5l8 5 8-5V7l-8 5z"/></svg>
    </li>
    <li>www.website.com
      <svg viewBox="0 0 24 24"><path d="M12 2a10 10 0 1 0 0 20 10 10 0 0 0 0-20zm6.9 6h-3a15 15 0 0 0-1.4-3.9A8 8 0 0 1 18.9 8zM12 4c.8 1.2 1.5 2.5 1.9 4h-3.8c.4-1.5 1.1-2.8 1.9-4zM4.3 14a8 8 0 0 1 0-4h3.4a16 16 0 0 0 0 4zm.8 2h3a15 15 0 0 0 1.4 3.9A8 8 0 0 1 5.1 16zm3-8h-3a8 8 0 0 1 4.4-3.9A15 15 0 0 0 8.1 8zM12 20c-.8-1.2-1.5-2.5-1.9-4h3.8c-.4 1.5-1.1 2.8-1.9 4zm2.3-6H9.7a14 14 0 0 1 0-4h4.6a14 14 0 0 1 0 4zm.2 5.9a15 15 0 0 0 1.4-3.9h3a8 8 0 0 1-4.4 3.9zm1.8-5.9a16 16 0 0 0 0-4h3.4a8 8 0 0 1 0 4z"/></svg>
    </li>
  </ul>
</section>

<section class="card card--back">
  <div class="wordmark">
    <span class="wordmark__main">DEL Varosi</span>
    <span class="wordmark__sub">Group</span>
  </div>
</section>

</body>
</html>
```